Kestrel Facilities Business Card Design

We would now like to design business cards with the new Kestrel Facilities logo

Target Market(s)

Professional

Industry/Entity Type

Professional services

Contact Information for Business Card

Employee name, title, phone number, email address, corporate office address and logo.

Font styles to use
Sans Serif

Colors
0054AA
0677BA
7BADD7
CADEEF
E8F1F8

Requirements
Must have
• My logo
Should not have
• any other pictures or images besides my logo

```html
<!DOCTYPE html>
<html lang="en">
<head>
<meta charset="utf-8">
<title>Kestrel Facilities Business Card</title>
<link rel="stylesheet" href="https://fonts.googleapis.com/css2?family=Montserrat:wght@400;500;700&display=swap">
<style>
  :root {
    --brand-blue: #3a7bc4;
    --brand-deep: #0054aa;
    --swoosh-grey: #a9a9a9;
    --card-white: #ffffff;
    --ink: #1c1c1c;
    --backdrop: #8f8f8f;
  }
  * { box-sizing: border-box; margin: 0; padding: 0; }
  html, body { width: 1200px; height: 900px; overflow: hidden; }
  body {
    background: var(--backdrop);
    font-family: "Montserrat", sans-serif;
    display: flex;
    flex-direction: column;
    align-items: center;
    justify-content: center;
    gap: 60px;
  }
  .card {
    position: relative;
    width: 600px;
    height: 343px;
    background: var(--card-white);
    border-radius: 22px;
    overflow: hidden;
    box-shadow: 0 10px 24px rgba(0,0,0,0.25);
  }
  .wordmark {
    display: flex;
    align-items: center;
    gap: 12px;
    color: var(--brand-blue);
    font-weight: 700;
    letter-spacing: 0.5px;
    line-height: 1;
  }
  .wordmark__square {
    width: 30px;
    height: 30px;
    background: var(--brand-blue);
  }
  .card--front { display: flex; align-items: center; justify-content: center; }
  .card--front .wordmark { font-size: 34px; }

  .card--back .wordmark {
    position: absolute;
    top: 62px;
    right: 34px;
    font-size: 22px;
  }
  .card--back .wordmark__square { width: 22px; height: 22px; }
  .swoosh { position: absolute; inset: 0; }
  .holder { position: absolute; left: 40px; top: 142px; }
  .holder__name {
    color: var(--brand-blue);
    font-weight: 700;
    font-size: 22px;
    letter-spacing: 0.3px;
  }
  .holder__title {
    color: var(--ink);
    font-size: 14px;
    margin-top: 4px;
  }
  .contact {
    position: absolute;
    left: 46px;
    top: 244px;
    list-style: none;
    color: var(--card-white);
    font-size: 12.5px;
    line-height: 17px;
  }
  .contact li { display: flex; align-items: center; gap: 6px; }
  .contact svg { width: 12px; height: 12px; flex: none; }
  .contact .indent { padding-left: 0; }
</style>
</head>
<body>
  <section class="card card--front">
    <div class="wordmark"><span class="wordmark__square"></span>Kestrel Facilities</div>
  </section>

  <section class="card card--back">
    <svg class="swoosh" viewBox="0 0 600 343" preserveAspectRatio="none" aria-hidden="true">
      <path d="M0,228 C110,178 260,160 400,158 C480,157 560,140 600,112"
            fill="none" stroke="var(--swoosh-grey)" stroke-width="7"/>
      <path d="M0,343 L0,240 C110,192 270,176 410,170 C500,166 568,130 600,96 L600,343 Z"
            fill="var(--brand-blue)"/>
      <path d="M340,168 C460,160 540,140 600,100" fill="none" stroke="var(--card-white)" stroke-width="3"/>
    </svg>

    <div class="wordmark"><span class="wordmark__square"></span>Kestrel Facilities</div>

    <div class="holder">
      <p class="holder__name">DARREN HOLLOWAY</p>
      <p class="holder__title">Co-Founder</p>
    </div>

    <ul class="contact">
      <li class="indent">4810 N. Harbor Lane</li>
      <li class="indent">Suite 208 Brookvale.14</li>
      <li>
        <svg viewBox="0 0 12 12"><path d="M2 1h2l1 3-1.5 1a7 7 0 0 0 3.5 3.5L8 7l3 1v2a1 1 0 0 1-1 1A9 9 0 0 1 1 2a1 1 0 0 1 1-1z" fill="#fff"/></svg>
        +254-317-42095
      </li>
      <li>
        <svg viewBox="0 0 12 12"><rect x="0.5" y="2.5" width="11" height="7" fill="none" stroke="#fff"/><path d="M0.5 2.5 6 7l5.5-4.5" fill="none" stroke="#fff"/></svg>
        info@kestrelfm.com
      </li>
      <li>
        <svg viewBox="0 0 12 12"><circle cx="6" cy="6" r="5.3" fill="none" stroke="#fff"/><ellipse cx="6" cy="6" rx="2.2" ry="5.3" fill="none" stroke="#fff"/><path d="M0.7 6h10.6" stroke="#fff"/></svg>
        www.kestrelfm.com
      </li>
    </ul>
  </section>
</body>
</html>
```